Business Card design which attached logo. Company is called Crestline Shield and main colours are Orange & Black.

Company specialises in Paint Protection and Detailing for supercars.

Details needed on business card:

Sales

Address: Unit 14, 517 Hadley Road, Fernvale Heights, FH 2907

Phone: 02 6194 2738

website: www.crestlineshield.com.au

Email: sales@crestlineshield.com.au

```html
<!DOCTYPE html>
<html lang="en">
<head>
<meta charset="utf-8">
<title>Crestline Shield — Business Card</title>
<link href="https://fonts.googleapis.com/css2?family=Raleway:wght@300;400&display=swap" rel="stylesheet">
<style>
  :root {
    --backdrop: #2b2c2f;
    --card-black: #0b0b0c;
    --card-white: #ffffff;
    --orange: #e8622a;
    --ink: #5f5f62;
    --ink-soft: #7a7a7d;
  }
  * { margin: 0; padding: 0; box-sizing: border-box; }
  html, body { width: 1200px; height: 900px; overflow: hidden; }
  body {
    background: var(--backdrop);
    font-family: "Raleway", sans-serif;
    position: relative;
  }
  .card {
    position: absolute;
    box-shadow: 0 18px 40px rgba(0,0,0,0.45);
  }

  /* Front: horizontal black card */
  .card-front {
    left: 520px; top: 280px;
    width: 580px; height: 330px;
    background: var(--card-black);
    display: flex; align-items: center; justify-content: center;
  }
  .brand {
    display: flex; align-items: center; gap: 12px;
    color: var(--orange);
    font-weight: 300;
    letter-spacing: 0.06em;
    text-transform: uppercase;
    white-space: nowrap;
  }
  .brand-dot {
    width: 10px; height: 10px; border-radius: 50%;
    background: var(--orange);
    flex: none;
  }
  .card-front .brand { font-size: 34px; }

  /* Back: vertical card with black top and white body */
  .card-back {
    left: 110px; top: 160px;
    width: 340px; height: 590px;
    background: var(--card-white);
    overflow: hidden;
  }
  .brand-band {
    height: 196px;
    background: var(--card-black);
    display: flex; align-items: center; justify-content: center;
    border-bottom: 3px solid var(--card-white);
    box-shadow: 0 3px 0 var(--orange);
  }
  .card-back .brand { font-size: 22px; gap: 9px; }
  .card-back .brand-dot { width: 8px; height: 8px; }

  .details { padding: 48px 34px 0 44px; }
  .person-name {
    font-size: 30px; font-weight: 300;
    letter-spacing: 0.08em;
    color: var(--ink);
    text-transform: uppercase;
    line-height: 1.2;
  }
  .name-rule {
    height: 2px; background: var(--orange);
    margin: 16px 0 18px; width: 245px;
  }
  .address {
    font-size: 15px; line-height: 1.5;
    color: var(--ink-soft);
    margin-bottom: 24px;
  }
  .contact {
    display: grid;
    grid-template-columns: 22px 1fr;
    column-gap: 16px;
    row-gap: 8px;
    align-items: center;
    font-size: 15px;
    color: var(--ink-soft);
  }
  .stem { width: 2px; height: 22px; background: var(--orange); justify-self: center; }
  .contact svg { display: block; }
</style>
</head>
<body>

  <section class="card card-front" aria-label="Card front">
    <div class="brand"><span class="brand-dot"></span>Crestline Shield</div>
  </section>

  <section class="card card-back" aria-label="Card back">
    <div class="brand-band">
      <div class="brand"><span class="brand-dot"></span>Crestline Shield</div>
    </div>
    <div class="details">
      <h1 class="person-name">Marcus Hale</h1>
      <div class="name-rule"></div>
      <p class="address">Unit 14, 517 Hadley Road<br>Fernvale Heights, FH 2907</p>
      <div class="contact">
        <span class="stem" aria-hidden="true"></span><span></span>

        <svg width="20" height="20" viewBox="0 0 20 20" aria-hidden="true">
          <circle cx="10" cy="10" r="10" fill="var(--orange)"/>
          <path d="M7 5.5c-.8.4-1.5 1.3-1.2 2.6.6 2.6 3.3 5.5 6 6.2 1.2.3 2-.3 2.5-1l-1.7-1.5-1.2.7c-1-.5-2.3-1.9-2.7-2.9l.7-1.2z" fill="#fff"/>
        </svg>
        <span class="phone">02 6194 2738</span>

        <svg width="20" height="20" viewBox="0 0 20 20" aria-hidden="true">
          <circle cx="10" cy="10" r="10" fill="var(--orange)"/>
          <rect x="5" y="6.5" width="10" height="7" fill="none" stroke="#fff" stroke-width="1.3"/>
          <path d="M5 6.5l5 4 5-4" fill="none" stroke="#fff" stroke-width="1.3"/>
        </svg>
        <span class="email">sales@crestlineshield.com.au</span>

        <svg width="20" height="20" viewBox="0 0 20 20" aria-hidden="true">
          <circle cx="10" cy="10" r="10" fill="var(--orange)"/>
          <circle cx="10" cy="10" r="5" fill="none" stroke="#fff" stroke-width="1.2"/>
          <ellipse cx="10" cy="10" rx="2.2" ry="5" fill="none" stroke="#fff" stroke-width="1.1"/>
          <path d="M5 10h10" stroke="#fff" stroke-width="1.1"/>
        </svg>
        <span class="web">www.crestlineshield.com.au</span>

        <span class="stem" aria-hidden="true"></span><span></span>
      </div>
    </div>
  </section>

</body>
</html>
```